Morvale Labs" Journey Swab Kit" Instructions Cards

We need to design two 4.25" x 5.5" 2-sided COVID-19 Specimen Collection Instructions Cards. One card is for the collection and testing of RT-PCR Nasal Swab Specimen and the second card is for the collection and testing of a Rapid Antigen Nasal Swab specimen.

Each card will be 4.25" x 5.5", 2-sided, laminated no-edge seal, with 3 color front and 2 color back.

RT-PCR Nasal Swab Collection Kit Instructions:
1. Please see an "example only" of a collection test kit instructions done for PCR Saliva test (see attached 2-sided card).
2. Please see attached PDF of the RT-PCR Nasal Swab Collection instructions. We will need to follow these collection steps instructions but design our own illustrations. With this set of instructions we will have a total of 8 steps.
3. Please see our Nasal Swab Collection device (see attached images), as our nasal swab is a dry collection device.

Rapid Antigen Nasal Swab Collection Kit Instructions:
1. Please see an "example" of a collection test kit instructions done for Rapid Antigen Test (see attached image with instructions). we will need to follow these steps 7 steps and will revise/shorten the copy.
2. We will have a total of 8 steps and will provide detailed copy for each step.

Please email me with any questions you may have: tpalwick@morvalediagnostics.example

Thank you

Ted

```html
<!DOCTYPE html>
<html lang="en">
<head>
<meta charset="utf-8">
<title>Morvale Labs Journey Swab Kit – RT-PCR Nasal Swab Instructions</title>
<link rel="stylesheet" href="https://fonts.googleapis.com/css2?family=Montserrat:wght@600;700&family=Open+Sans:wght@400&display=swap">
<style>
  :root {
    --backdrop: #6e6e6e;
    --card-blue: #2f68bd;
    --heading-blue: #2f6bc0;
    --badge-green: #6cbd45;
    --ink: #161616;
    --body-ink: #222222;
    --paper: #ffffff;
    --art-white: #f4f6f9;
    --art-grey: #d5dbe3;
    --art-skin: #8a5a3c;
    --art-skin-dark: #5e3a25;
    --art-blue: #a9c6ea;
  }
  * { box-sizing: border-box; margin: 0; padding: 0; }
  html, body {
    width: 1200px; height: 840px; overflow: hidden;
    background: var(--backdrop);
  }
  .canvas { position: relative; width: 1200px; height: 840px; }

  .card {
    position: absolute; top: 90px;
    width: 521px; height: 673px;
    background: var(--paper);
    border: 15px solid var(--card-blue);
  }
  .card--front { left: 63px; }
  .card--back { left: 622px; }

  .card__title {
    position: absolute; top: 44px; left: 0; right: 0;
    text-align: center;
    font-family: "Montserrat", sans-serif; font-weight: 700;
    font-size: 29.5px; line-height: 38px; color: var(--ink);
    letter-spacing: 0.2px;
  }

  .steps {
    position: absolute; top: 151px; left: 36px; right: 16px;
    list-style: none;
  }
  .step {
    position: relative; height: 102.5px;
    display: flex; align-items: center;
  }
  .step__art {
    position: relative; flex: 0 0 86px; height: 86px;
    border-radius: 50%;
    border: 3px solid var(--card-blue);
    background: var(--paper);
  }
  .step__art::before {
    content: ""; position: absolute; inset: 9px; border-radius: 50%;
    background: radial-gradient(circle at 50% 45%, var(--art-white) 0%, var(--art-grey) 100%);
  }
  .step__art--skin::before {
    background: radial-gradient(circle at 50% 40%, var(--art-skin) 0%, var(--art-skin-dark) 100%);
  }
  .step__art--lab::before {
    background: radial-gradient(circle at 50% 45%, var(--art-white) 0%, var(--art-blue) 100%);
  }
  .step__number {
    position: absolute; top: -12px; left: 12px; z-index: 1;
    width: 29px; height: 29px; border-radius: 50%;
    background: var(--badge-green); color: var(--paper);
    font-family: "Montserrat", sans-serif; font-weight: 700;
    font-size: 13px; line-height: 29px; text-align: center;
  }
  .step__text { margin-left: 13px; width: 322px; margin-top: -6px; }
  .step__heading {
    font-family: "Montserrat", sans-serif; font-weight: 600;
    font-size: 17.5px; line-height: 22px; color: var(--heading-blue);
    margin-bottom: 6px;
  }
  .step__body {
    font-family: "Open Sans", sans-serif; font-weight: 400;
    font-size: 10.8px; line-height: 14.2px; color: var(--body-ink);
  }

  .brand {
    position: absolute; top: 562px; left: 0; right: 0;
    display: flex; justify-content: center; align-items: center; gap: 10px;
  }
  .brand__mark {
    width: 24px; height: 24px; border-radius: 50%;
    background: var(--card-blue);
  }
  .brand__name {
    font-family: "Montserrat", sans-serif; font-weight: 600;
    font-size: 31px; line-height: 40px; color: var(--ink);
    letter-spacing: 0.5px;
  }
  .brand__site {
    position: absolute; top: 624px; left: 0; right: 0;
    text-align: center;
    font-family: "Montserrat", sans-serif; font-weight: 600;
    font-size: 12px; color: var(--ink); letter-spacing: 1.2px;
  }
</style>
</head>
<body>
<main class="canvas">

  <section class="card card--front" aria-label="Instructions card, steps 1 to 4">
    <h1 class="card__title">RT-PCR Nasal Swab<br>Collection Kit Instructions:</h1>
    <ol class="steps">
      <li class="step">
        <div class="step__art" role="img" aria-label="Illustration of opened collection kit with tube, swab and biohazard bag"><span class="step__number">01</span></div>
        <div class="step__text">
          <h2 class="step__heading">Remove contents</h2>
          <p class="step__body">where you will open the collection kit. Remove and lay out contents of kit. Read instructions before starting specimen collection.</p>
        </div>
      </li>
      <li class="step">
        <div class="step__art" role="img" aria-label="Illustration of hands pulling the swab from its package"><span class="step__number">02</span></div>
        <div class="step__text">
          <h2 class="step__heading">Remove the swab</h2>
          <p class="step__body">from the package. Do not touch the soft end with your hands or anything else.</p>
        </div>
      </li>
      <li class="step">
        <div class="step__art step__art--skin" role="img" aria-label="Illustration of a person inserting the swab into a nostril"><span class="step__number">03</span></div>
        <div class="step__text">
          <h2 class="step__heading">Insert &amp; slowly rotate</h2>
          <p class="step__body">the swab, gently pressing against the inside of each nostril at least 4 times for a total of 15 seconds. Get as much nasal discharge as possible on the soft end of the swab.</p>
        </div>
      </li>
      <li class="step">
        <div class="step__art step__art--skin" role="img" aria-label="Illustration of a person removing the swab from the nostril"><span class="step__number">04</span></div>
        <div class="step__text">
          <h2 class="step__heading">Gently remove the swab.</h2>
        </div>
      </li>
    </ol>
    <div class="brand"><span class="brand__mark" aria-hidden="true"></span><span class="brand__name">MORVALE</span></div>
    <p class="brand__site">www.MorvaleDiagnostics.example</p>
  </section>

  <section class="card card--back" aria-label="Instructions card, steps 5 to 8">
    <h1 class="card__title">RT-PCR Nasal Swab<br>Collection Kit Instructions:</h1>
    <ol class="steps">
      <li class="step">
        <div class="step__art" role="img" aria-label="Illustration of hands snapping the swab into the sterile tube"><span class="step__number">05</span></div>
        <div class="step__text">
          <h2 class="step__heading">Place the swab</h2>
          <p class="step__body">in the sterile tube and snap off the end of the swab at the break line, so that it fits comfortably in the tube. Place the cap on the tube and screw down tightly to prevent leakage.</p>
        </div>
      </li>
      <li class="step">
        <div class="step__art" role="img" aria-label="Illustration of the tube going into the biohazard bag"><span class="step__number">06</span></div>
        <div class="step__text">
          <h2 class="step__heading">Place the tube</h2>
          <p class="step__body">containing the swab in the biohazard bag provided and seal the bag. and follow the instructions on the card for shipping to lab for testing.</p>
        </div>
      </li>
      <li class="step">
        <div class="step__art step__art--lab" role="img" aria-label="Illustration of an RT-PCR laboratory machine"><span class="step__number">07</span></div>
        <div class="step__text">
          <h2 class="step__heading">RT-PCR Machine</h2>
          <p class="step__body">the sample is loaded into the RT-PCR machine at our lab, which copies and detects any viral genetic material. Processing takes only a few hours once your kit arrives.</p>
        </div>
      </li>
      <li class="step">
        <div class="step__art step__art--lab" role="img" aria-label="Illustration of a test result report with a virus icon"><span class="step__number">08</span></div>
        <div class="step__text">
          <h2 class="step__heading">Result</h2>
          <p class="step__body">your test result is sent to you by secure email or text message within 24 to 48 hours. Keep this card until you receive your result and share it as required.</p>
        </div>
      </li>
    </ol>
    <div class="brand"><span class="brand__mark" aria-hidden="true"></span><span class="brand__name">MORVALE</span></div>
    <p class="brand__site">www.MorvaleDiagnostics.example</p>
  </section>

</main>
</body>
</html>
```